Business Card Design

New business card design

Target Market(s)

Residential & Commercial Property Managers

Industry/Entity Type

Plumbing Services

Contact Information for Business Card

Name - Rowan Keddle, title - Director, Phone Number - 0431 286 517, email - rowan@tbk-plumbing.com.au, Company ABN - 73 215 904 386,

Font styles to use
Sans Serif

Colors
0054AA
0677BA
7BADD7
CADEEF
E8F1F8

```html
<!DOCTYPE html>
<html lang="en">
<head>
<meta charset="utf-8">
<title>TBK Plumbing Services – Business Cards</title>
<link href="https://fonts.googleapis.com/css2?family=Montserrat:wght@300;400;700&display=swap" rel="stylesheet">
<style>
  :root {
    --stage: #e9edf1;
    --card: #ffffff;
    --ink: #1f2328;
    --muted: #6f6a66;
    --aqua: #29a8e0;
    --edge: #2aa3dc;
  }
  * { margin: 0; padding: 0; box-sizing: border-box; }
  html, body { width: 1200px; height: 913px; overflow: hidden; }
  body {
    background: var(--stage);
    font-family: "Montserrat", sans-serif;
    position: relative;
  }
  .card {
    position: absolute;
    width: 540px;
    height: 320px;
    background: var(--card);
    border-radius: 22px;
    box-shadow: 0 4px 0 var(--edge), 0 14px 30px rgba(20, 40, 60, .18);
    overflow: hidden;
  }
  .card--front { left: 40px; top: 296px; }
  .card--back { left: 620px; top: 296px; }

  .brand { color: var(--ink); font-weight: 300; white-space: nowrap; }
  .card--front .brand {
    position: absolute; left: 0; right: 0; top: 136px;
    text-align: center;
    font-size: 31px; letter-spacing: 2px;
  }
  .card--back .brand {
    position: absolute; right: 30px; top: 34px;
    font-size: 21px; letter-spacing: 2px; text-align: right;
  }

  .wave { position: absolute; left: 0; top: 0; width: 540px; height: 320px; }

  .accent-bar {
    position: absolute; left: 0; top: 168px;
    width: 14px; height: 62px; background: var(--aqua);
  }
  .person { position: absolute; left: 34px; top: 166px; }
  .person__name { color: var(--aqua); font-weight: 700; font-size: 25px; line-height: 1.1; }
  .person__title { color: var(--ink); font-weight: 400; font-size: 18px; margin-top: 2px; }

  .contact { position: absolute; left: 34px; top: 250px; list-style: none; }
  .contact li {
    display: flex; align-items: center; gap: 8px;
    font-size: 16px; color: var(--ink); line-height: 1.55;
  }
  .contact svg { width: 15px; height: 15px; flex: none; }

  .abn {
    position: absolute; right: 28px; top: 218px;
    font-size: 14px; color: var(--ink); white-space: nowrap;
  }
</style>
</head>
<body>
  <section class="card card--front" aria-label="Card front">
    <p class="brand">TBK Plumbing Services</p>
  </section>

  <section class="card card--back" aria-label="Card back">
    <p class="brand">TBK Plumbing Services</p>

    <svg class="wave" viewBox="0 0 540 320" aria-hidden="true">
      <path d="M64 238 L296 198 Q312 194 330 192 L520 108" fill="none" stroke="var(--aqua)" stroke-width="1.6"/>
      <path d="M64 243 L300 202 Q318 199 338 197 L520 114" fill="none" stroke="var(--aqua)" stroke-width="1"/>
    </svg>

    <div class="accent-bar"></div>
    <div class="person">
      <p class="person__name">Rowan Keddle</p>
      <p class="person__title">Director</p>
    </div>

    <p class="abn">Company ABN - 73 215 904 386</p>

    <ul class="contact">
      <li>
        <svg viewBox="0 0 24 24"><path d="M6.6 10.8a15 15 0 0 0 6.6 6.6l2.2-2.2a1 1 0 0 1 1-.25 11.4 11.4 0 0 0 3.6.57 1 1 0 0 1 1 1V20a1 1 0 0 1-1 1A17 17 0 0 1 3 4a1 1 0 0 1 1-1h3.5a1 1 0 0 1 1 1c0 1.25.2 2.45.57 3.57a1 1 0 0 1-.25 1z" fill="var(--aqua)"/></svg>
        0431 286 517
      </li>
      <li>
        <svg viewBox="0 0 24 24"><rect x="2" y="5" width="20" height="14" rx="2" fill="var(--aqua)"/><path d="M3 6l9 7 9-7" fill="none" stroke="#fff" stroke-width="1.6"/></svg>
        rowan@tbk-plumbing.com.au
      </li>
    </ul>
  </section>
</body>
</html>
```